Italian restaurant needs new site

Need to make our website better.

Must have reservation module

Must be able to sell wine tasting tours and wine pairing tours and intégrate with dunmo desk

Blog

Social media

Wandervane ranking and last review.
Updates

Number of Pages Required

1 page

Font styles to use
Serif

Requirements
Must have
• Reservation module
• Marketplace to buy wine pairings and gift certificates
• Wandervane review
• Kindlepost posts
• All info from old site

```html
<!DOCTYPE html>
<html lang="en">
<head>
<meta charset="utf-8">
<title>Lumara Bistro – Italian Cuisine &amp; Wine Bar</title>
<link href="https://fonts.googleapis.com/css2?family=Open+Sans:wght@400;600;700;800&display=swap" rel="stylesheet">
<style>
:root{
  --wine:#8b1e24;
  --ink:#222;
  --text:#555;
  --line:#d9d9d9;
  --paper:#fff;
  --mist:#ededed;
}
*{box-sizing:border-box;margin:0;padding:0}
html,body{width:1200px;height:4408px;overflow:hidden}
body{position:relative;background:var(--paper);font-family:"Open Sans",Arial,sans-serif;color:var(--text)}
.abs{position:absolute}
.section{position:absolute;left:0;width:1200px}
.photo{position:absolute}

/* header */
.site-header{top:0;height:74px;background:#fff;z-index:5}
.nav a{position:absolute;top:26px;font-size:11px;font-weight:600;color:var(--ink);text-decoration:none;letter-spacing:.2px;line-height:20px}
.nav a.active{background:var(--wine);color:#fff;padding:0 12px;top:25px}
.search{position:absolute;left:1036px;top:19px;width:34px;height:34px;border-radius:50%;background:var(--wine)}
.logo-disc{position:absolute;left:86px;top:-46px;width:268px;height:268px;border-radius:50%;background:#fff;z-index:6;display:flex;align-items:flex-end;justify-content:center;padding-bottom:86px}
.brand{font-family:"Open Sans",Arial,sans-serif;color:var(--wine);font-size:26px;font-weight:700;letter-spacing:.5px;line-height:1;text-transform:uppercase}

/* hero */
.hero{top:74px;height:650px;background:linear-gradient(100deg,#4a4540 0%,#8a7f72 35%,#b9b0a4 55%,#6d5f52 80%,#3c332d 100%)}
.hero-title{left:132px;top:276px;font-size:41px;font-weight:800;color:#fff;line-height:45px;letter-spacing:.5px}
.btn{position:absolute;display:flex;align-items:center;justify-content:center;font-size:13px;font-weight:700;color:#fff;background:var(--wine);text-transform:uppercase}
.btn-outline{border:2px solid #fff}
.dots{position:absolute;display:flex;gap:14px}
.dots i{display:block;width:9px;height:9px;border-radius:50%;background:#fff}
.dots i.on{background:transparent;border:2px solid #fff;width:11px;height:11px;margin-top:-1px}

/* welcome */
.welcome{top:724px;height:512px}
.welcome-box{left:132px;top:87px;width:613px;height:334px;border:1px solid var(--line)}
.h-section{font-size:26px;font-weight:800;color:var(--wine);letter-spacing:.3px}
.welcome p{position:absolute;left:183px;top:180px;width:378px;font-size:12.5px;line-height:21px;text-align:justify;color:var(--text)}
.framed{border:5px solid #fff;box-shadow:0 1px 4px rgba(0,0,0,.15)}

/* tasting */
.tasting{top:1236px;height:490px;background:linear-gradient(90deg,#6f7466 0%,#8c8a78 35%,#a7a191 60%,#5e5b4e 100%)}
.tasting-copy{position:absolute;left:240px;width:370px;text-align:center;color:#fff}

/* products */
.products{top:1726px;height:614px}
.product{position:absolute;top:166px;width:160px;text-align:center}
.product-photo{margin:0 auto;width:130px;height:340px}
.product h3{font-size:12px;font-weight:700;color:var(--ink);margin-top:24px}

/* reservations */
.reservations{top:2340px;height:596px;background:var(--wine)}
.field{position:absolute;height:48px;border:1px solid rgba(255,255,255,.85);color:#fff;font-size:12px;padding:15px 18px}
.book{position:absolute;left:878px;top:481px;width:146px;height:40px;background:#fff;color:var(--wine);font-size:15px;font-weight:700;display:flex;align-items:center;justify-content:center}

/* blog */
.blog{top:2936px;height:553px;background:var(--mist)}
.post{position:absolute;top:164px;width:265px}
.post .photo{position:static;width:265px;height:189px}
.post h4{font-size:11px;font-weight:700;color:var(--ink);line-height:17px;margin-top:20px;width:230px}
.post p{font-size:10.5px;line-height:16px;color:var(--text);margin-top:6px}
.post .more{display:block;font-size:11px;font-weight:700;color:var(--wine);margin-top:20px}

/* review */
.review{top:3489px;height:534px;background:#fff}
.review-source{position:absolute;top:96px;left:0;width:1200px;text-align:center;font-size:17px;font-weight:700;color:var(--ink)}
.review-source .mark{display:inline-block;width:14px;height:14px;border-radius:50%;background:var(--wine);vertical-align:-1px;margin-right:5px}
.card{position:absolute;top:158px;width:440px;height:265px;border:1px solid var(--line);padding:38px 40px}
.card h4{font-size:11px;font-weight:700;color:var(--ink)}
.card p{font-size:11px;line-height:20px;color:var(--text);margin-top:14px;width:340px}
.reviewer{position:absolute;left:42px;top:178px;display:flex;align-items:center;gap:16px;font-size:11px;color:var(--text)}
.avatar{width:40px;height:40px;background:linear-gradient(135deg,#8a6a55,#d1b49a)}
.pager{position:absolute;top:462px;left:554px;display:flex;gap:11px}
.pager i{display:block;width:9px;height:9px;border-radius:50%;background:#c8c8c8}
.pager i.on{background:var(--wine)}

/* footer */
.site-footer{top:4023px;height:385px;background:var(--mist)}
.foot-brand{position:absolute;left:132px;top:110px;width:170px;text-align:center}
.foot-brand .brand{font-size:22px}
.foot-h{position:absolute;top:66px;font-size:12px;font-weight:700;color:var(--wine)}
.foot-list{position:absolute;top:100px;font-size:11.5px;line-height:20px;color:var(--text);list-style:none}
.foot-btn{position:absolute;left:400px;top:182px;width:110px;height:29px;background:var(--wine);color:#fff;font-size:11px;font-weight:700;display:flex;align-items:center;justify-content:center}
.feed{position:absolute;left:876px;top:57px;width:194px;height:178px;background:#fff;border:1px solid var(--line)}
.feed-cover{height:92px;background:linear-gradient(135deg,#5a1a22,#9b3b3a);position:relative;padding:8px}
.feed-cover b{color:#fff;font-size:13px;font-weight:700;display:block;margin-left:48px}
.feed-cover span{color:#fff;font-size:9px;margin-left:48px;display:block}
.feed-thumb{position:absolute;left:8px;top:8px;width:40px;height:40px;background:#c99;border:2px solid #fff}
.feed-follow{position:absolute;left:8px;bottom:8px;background:#fff;color:var(--ink);font-size:9px;font-weight:600;padding:2px 6px}
.feed p{font-size:9px;color:var(--text);padding:8px 12px 0;line-height:13px}
.feed-faces{display:flex;gap:4px;padding:6px 12px}
.feed-faces i{display:block;width:22px;height:22px;background:linear-gradient(135deg,#8d7a88,#c9a9a0)}
.rule{position:absolute;left:132px;top:288px;width:938px;height:1px;background:var(--line)}
.follow{position:absolute;left:132px;top:335px;font-size:12px;font-weight:700;color:var(--wine)}
.social{position:absolute;top:331px;width:24px;height:24px;border-radius:50%;background:var(--wine)}
.copyright{position:absolute;right:130px;top:337px;font-size:10px;color:var(--ink)}
</style>
</head>
<body>

<header class="section site-header">
  <div class="logo-disc">
    <span class="brand">Lumara Bistro</span>
  </div>
  <nav class="nav">
    <a class="active" style="left:599px">HOME</a>
    <a style="left:676px">ABOUT US</a>
    <a style="left:760px">PRODUCTS</a>
    <a style="left:846px">RESERVATION</a>
    <a style="left:940px">CONTACT US</a>
  </nav>
  <div class="search">
    <svg width="34" height="34" viewBox="0 0 34 34"><circle cx="16" cy="16" r="4" fill="none" stroke="#fff" stroke-width="2"/><line x1="19" y1="19" x2="22" y2="22" stroke="#fff" stroke-width="2"/></svg>
  </div>
</header>

<section class="section hero" role="img" aria-label="Red wine being poured from a bottle into a glass in a softly lit bar">
  <h1 class="abs hero-title">ITALIAN CUISING<br>&amp; WINE BAR</h1>
  <a class="btn btn-outline" style="left:135px;top:390px;width:194px;height:55px">READ MORE&nbsp;&nbsp;<svg width="7" height="9" viewBox="0 0 7 9"><path d="M0 0L7 4.5L0 9Z" fill="#fff"/></svg></a>
  <div class="dots" style="left:549px;top:586px"><i></i><i class="on"></i><i></i><i></i><i></i></div>
</section>

<section class="section welcome">
  <div class="abs welcome-box"></div>
  <h2 class="abs h-section" style="left:183px;top:130px">WELCOME TO OUR SITE</h2>
  <p>Lumara Bistro Located in the heart of downtown, across from Corvel Square, just two short blocks up from Halden Resort and the Porto Salvia marina is Lumara Bistro, a place with great original Southern Italian and Mediterranean cuisine and a European touch.</p>
  <a class="btn" style="left:183px;top:312px;width:161px;height:49px">READ MORE</a>
  <div class="photo" role="img" aria-label="Overhead view of shared dishes, flatbreads, curries and rice" style="left:745px;top:67px;width:265px;height:368px;background:linear-gradient(160deg,#6b4a2e,#a77a4e 55%,#c9ae88)"></div>
  <div class="photo framed" role="img" aria-label="Warmly lit restaurant interior with guests at tables" style="left:632px;top:124px;width:158px;height:172px;background:linear-gradient(180deg,#7a2f1e,#4a2418)"></div>
  <div class="photo framed" role="img" aria-label="Plated salad with grilled chicken" style="left:909px;top:241px;width:158px;height:178px;background:linear-gradient(160deg,#e9e3da,#b8a88a)"></div>
</section>

<section class="section tasting" role="img" aria-label="Woman smelling a glass of red wine at a tasting">
  <div class="tasting-copy" style="top:112px">
    <h2 style="font-size:26px;font-weight:800;letter-spacing:.3px">WINE TASTING TOURS</h2>
    <p style="font-size:17px;line-height:24px;margin-top:20px">Lorem Ipsum is simply dummy text of the printing and typesetting industry. Lorem Ipsum has been the industry's</p>
  </div>
  <a class="btn btn-outline" style="left:346px;top:284px;width:159px;height:48px">READ MORE</a>
</section>

<section class="section products">
  <h2 class="h-section" style="position:absolute;top:66px;width:1200px;text-align:center">OUR PRODUCTS</h2>
  <div class="product" style="left:156px">
    <div class="product-photo" role="img" aria-label="Bottle of white wine" style="background:linear-gradient(180deg,#f6f3ec,#e9e1cc)"></div>
    <h3>HEADING 1</h3>
  </div>
  <div class="product" style="left:382px">
    <div class="product-photo" role="img" aria-label="Green bottle of white wine" style="background:linear-gradient(180deg,#f3f3ee,#d7d5a8)"></div>
    <h3>HEADING 2</h3>
  </div>
  <div class="product" style="left:632px">
    <div class="product-photo" role="img" aria-label="Dark bottle of red wine" style="background:linear-gradient(180deg,#f1eeee,#bdb7b8)"></div>
    <h3>HEADING 3</h3>
  </div>
  <div class="product" style="left:874px">
    <div class="product-photo" role="img" aria-label="Bottle of sparkling wine" style="background:linear-gradient(180deg,#f3f3f3,#d8dab0)"></div>
    <h3>HEADING 4</h3>
  </div>
</section>

<section class="section reservations">
  <h2 style="position:absolute;top:66px;width:1200px;text-align:center;font-size:26px;font-weight:800;color:#fff">RESERVATIONS</h2>
  <div class="field" style="left:193px;top:163px;width:262px">Name</div>
  <div class="field" style="left:474px;top:163px;width:262px">E mail</div>
  <div class="field" style="left:758px;top:163px;width:262px">Party Size</div>
  <div class="field" style="left:193px;top:231px;width:262px">Date</div>
  <div class="field" style="left:474px;top:231px;width:262px">Time</div>
  <div class="field" style="left:758px;top:231px;width:262px">Hotel Name</div>
  <div class="field" style="left:193px;top:307px;width:831px;height:147px">Message</div>
  <div class="book">BOOK NOW</div>
</section>

<section class="section blog">
  <h2 class="h-section" style="position:absolute;top:70px;width:1200px;text-align:center">LATEST BLOG</h2>
  <article class="post" style="left:134px">
    <div class="photo" role="img" aria-label="Silhouette of a diner at a table at sunset" style="background:linear-gradient(180deg,#2a2a30,#8a7a6a 55%,#1c1c20)"></div>
    <h4>LOREM IPSUM IS SIMPLY DUMMY TEXT OF THE PRINTING</h4>
    <p>There are many variations of passages of Lorem Ipsum available, but the majority</p>
    <span class="more">READ MORE</span>
  </article>
  <article class="post" style="left:466px">
    <div class="photo" role="img" aria-label="Guests raising wine glasses at a dinner" style="background:linear-gradient(135deg,#e8e4de,#9a8c80 50%,#d9d3cc)"></div>
    <h4>IT IS A LONG ESTABLISHED FACT THAT A READER WILL BE</h4>
    <p>There are many variations of passages of Lorem Ipsum available, but the majority</p>
    <span class="more">READ MORE</span>
  </article>
  <article class="post" style="left:805px">
    <div class="photo" role="img" aria-label="Wine bottles and a glass of red wine on a table" style="background:linear-gradient(135deg,#f1efe9,#b9b29e 60%,#e6e2dc)"></div>
    <h4>THERE ARE MANY VARIATIONS OF PASSAGES OF LOREM IPSUM</h4>
    <p>There are many variations of passages of Lorem Ipsum available, but the majority</p>
    <span class="more">READ MORE</span>
  </article>
</section>

<section class="section review">
  <h2 class="h-section" style="position:absolute;top:58px;width:1200px;text-align:center">REVIEW</h2>
  <div class="review-source"><span class="mark"></span>Wandervane</div>
  <div class="card" style="left:146px">
    <h4>DELICIOUS ITALIAN!</h4>
    <p>We went to Lumara Bistro the third night of our stay. The entire staff was very attentive, the food was amazing and we will definitely be back If you're looking to have amazing Italian food, be sure to visit this restaurant!</p>
    <div class="reviewer"><div class="avatar" role="img" aria-label="Reviewer photo"></div>Dalbury, Westmarch</div>
  </div>
  <div class="card" style="left:611px">
    <h4>WONDERFUL DINNER</h4>
    <p>love this place the service is great the food is great. had a wonderful time. Thanks, chef Tomas for a wonderful dinner.</p>
    <div class="reviewer"><div class="avatar" role="img" aria-label="Reviewer photo" style="background:linear-gradient(135deg,#0f5a4a,#3fbfa0)"></div>Elena R</div>
  </div>
  <div class="pager"><i></i><i></i><i class="on"></i><i></i><i></i></div>
</section>

<footer class="section site-footer">
  <div class="foot-brand">
    <div class="brand">Lumara Bistro</div>
  </div>
  <h4 class="foot-h" style="left:394px">CONTACT US</h4>
  <ul class="foot-list" style="left:397px">
    <li>Tel. 555 0148</li>
    <li>Avenida Brisa 12, L-3</li>
    <li>Porto Salvia, Costa Verde</li>
  </ul>
  <div class="foot-btn">RESERVATIONS</div>
  <h4 class="foot-h" style="left:656px">MENU</h4>
  <ul class="foot-list" style="left:658px">
    <li>Home</li><li>About us</li><li>Menu</li><li>Reservations</li><li>Contact us</li>
  </ul>
  <div class="feed">
    <div class="feed-cover">
      <div class="feed-thumb"></div>
      <b>Lumara Bistro</b>
      <span>3,464 follows</span>
      <div class="feed-follow">Follow page</div>
    </div>
    <p>Be the first of your friends to follow this.</p>
    <div class="feed-faces"><i></i><i></i><i></i><i></i><i></i><i></i></div>
  </div>
  <div class="rule"></div>
  <div class="follow">FOLLOW US</div>
  <div class="social" style="left:224px"></div>
  <div class="social" style="left:257px"></div>
  <div class="social" style="left:289px"></div>
  <div class="copyright">Copyrights @ 2017 All Rights Reserved</div>
</footer>

</body>
</html>
```